Business Card Design

We are a manufacturing and distribution company with most of our customer base being supermarkets. We have established brand guidelines that are attached.

```html
<!DOCTYPE html>
<html lang="en">
<head>
<meta charset="utf-8">
<title>Valmore Business Card</title>
<link rel="stylesheet" href="https://fonts.googleapis.com/css2?family=Archivo:wdth,wght@100..125,400;100..125,700&display=swap">
<style>
  :root {
    --bg: #e6e6e4;
    --paper: #ffffff;
    --ink: #1c1c1e;
    --accent-red: #e0141e;
    --brand-blue: #0066a8;
    --muted: #6b6b6b;
    --faint: #e8e8e8;
  }
  * { margin: 0; padding: 0; box-sizing: border-box; }
  html, body {
    width: 1200px; height: 802px; overflow: hidden;
    background: var(--bg);
    font-family: "Archivo", Arial, sans-serif;
  }
  .sheet {
    width: 1200px; height: 802px;
    display: flex; align-items: center; justify-content: center; gap: 60px;
  }
  .card {
    position: relative;
    width: 520px; height: 300px;
    background: var(--paper);
    border: 2px solid var(--accent-red);
    border-top-color: #f2f2f2;
    border-left-color: #f2f2f2;
    overflow: hidden;
  }
  .corner-shape { position: absolute; }

  /* front side */
  .card-front .corner-shape { top: -150px; right: -120px; width: 330px; height: 330px; border-radius: 50%; background: var(--faint); }
  .front-content { position: absolute; left: 44px; top: 58px; }
  .brand-name {
    font-weight: 700; font-stretch: 125%;
    color: var(--ink); letter-spacing: 0.02em; line-height: 1;
  }
  .card-front .brand-name { font-size: 28px; }
  .person-name { margin-top: 26px; font-size: 15px; color: var(--accent-red); font-stretch: 110%; letter-spacing: 0.02em; }
  .person-role { font-size: 13px; color: var(--muted); margin-top: 2px; }
  .address { margin-top: 18px; font-size: 13px; color: var(--muted); line-height: 1.35; }
  .contacts { margin-top: 16px; list-style: none; font-size: 13px; color: var(--muted); line-height: 1.4; }
  .contacts li { display: flex; align-items: center; gap: 8px; }
  .contacts svg { width: 12px; height: 12px; flex: none; }

  /* back side */
  .card-back .corner-shape { left: -140px; bottom: -170px; width: 340px; height: 340px; border-radius: 50%; background: var(--brand-blue); }
  .back-lockup {
    position: absolute; left: 210px; top: 128px;
    display: flex; align-items: center; gap: 12px;
  }
  .brand-square { width: 26px; height: 26px; background: var(--accent-red); }
  .card-back .brand-name { font-size: 36px; }
</style>
</head>
<body>
<main class="sheet">
  <section class="card card-front" aria-label="Card front">
    <div class="corner-shape"></div>
    <div class="front-content">
      <h1 class="brand-name">VALMORE</h1>
      <p class="person-name">DANIEL REYES</p>
      <p class="person-role">Manager</p>
      <p class="address">Your address, city<br>state, ZIP 0000</p>
      <ul class="contacts">
        <li>
          <svg viewBox="0 0 12 12"><path d="M2.5 1 L4.5 1 L5 3.6 L3.8 4.6 Q5 7.2 7.4 8.2 L8.4 7 L11 7.5 L11 9.5 Q10.5 11 9 11 Q1 10 1 3 Q1 1.5 2.5 1Z" fill="var(--accent-red)"/></svg>
          123-456-2100
        </li>
        <li>
          <svg viewBox="0 0 12 12"><rect x="1" y="2.5" width="10" height="7" fill="none" stroke="var(--accent-red)" stroke-width="1.2"/><path d="M1 2.5 L6 6.5 L11 2.5" fill="none" stroke="var(--accent-red)" stroke-width="1.2"/></svg>
          hello@valmore.com
        </li>
        <li>
          <svg viewBox="0 0 12 12"><circle cx="6" cy="6" r="5" fill="var(--accent-red)"/><path d="M1 6 H11 M6 1 Q3 6 6 11 M6 1 Q9 6 6 11" fill="none" stroke="#fff" stroke-width="0.8"/></svg>
          www.valmore.com
        </li>
      </ul>
    </div>
  </section>

  <section class="card card-back" aria-label="Card back">
    <div class="corner-shape"></div>
    <div class="back-lockup">
      <span class="brand-square"></span>
      <span class="brand-name">VALMORE</span>
    </div>
  </section>
</main>
</body>
</html>
```